Business Card for premium dental clinic

We are a premium dental clinic based in Brasov, Romania with more than 15 year on the market, providing quality dental treatment made by a team of more specialized dentists, working with modern equipment as a solution to beautiful and healthy teeth.

Our current logo for the clinic use 2 square with colors black and gold - dr Ternisu - studio, using family fonts Bodoni, Myriad Pro and Segoe Print.
Depending on the printing we used some gold CMYK background or gold foil picture background or a gold gradient.
We want a business card:
- eye catching business card
- distinguished business card
- premium design
- to keep the color scheme of black and gold
- to attract the customers to spent time reading the information
- modern concept

```html
<!DOCTYPE html>
<html lang="en">
<head>
<meta charset="utf-8">
<title>Business Card – dr Ternisu studio</title>
<link href="https://fonts.googleapis.com/css2?family=Roboto:wght@400;500&family=Ubuntu:wght@500&display=swap" rel="stylesheet">
<style>
  :root {
    --backdrop: #e9e9ea;
    --paper: #f4f4f2;
    --ink: #000000;
    --gold: #e2a521;
    --gold-light: #f7dc72;
    --gold-deep: #c98d12;
    --text-light: #ffffff;
    --text-dark: #222222;
  }
  * { margin: 0; padding: 0; box-sizing: border-box; }
  html, body {
    width: 1200px; height: 1069px; overflow: hidden;
    background: var(--backdrop);
  }
  .canvas {
    position: relative; width: 1200px; height: 1069px;
  }
  .card {
    position: absolute; left: 290px; width: 620px; height: 354px;
    box-shadow: 0 10px 28px rgba(0,0,0,0.14);
    overflow: hidden;
  }
  /* Front */
  .card-front { top: 150px; background: var(--paper); }
  .brand-lockup {
    position: absolute; left: 50%; top: 50%;
    transform: translate(-50%, -50%);
    display: flex; align-items: center; gap: 16px;
  }
  .brand-square {
    width: 34px; height: 34px; background: var(--gold);
  }
  .brand-name {
    font-family: "Roboto", sans-serif; font-weight: 400;
    font-size: 34px; color: var(--text-dark); letter-spacing: 0.5px;
  }
  /* Back */
  .card-back { top: 574px; display: flex; }
  .gold-foil {
    width: 262px; height: 100%;
    background:
      radial-gradient(ellipse at 30% 25%, var(--gold-light) 0%, transparent 55%),
      radial-gradient(ellipse at 70% 75%, var(--gold-light) 0%, transparent 50%),
      linear-gradient(135deg, var(--gold) 0%, var(--gold-light) 45%, var(--gold-deep) 100%);
  }
  .info-panel {
    flex: 1; background: var(--ink); color: var(--text-light);
    padding: 58px 30px 0 40px;
    font-family: "Roboto", sans-serif;
  }
  .person-name {
    font-family: "Ubuntu", sans-serif; font-weight: 500;
    font-size: 25px; color: var(--gold); line-height: 1.1;
  }
  .person-role { font-size: 14px; margin-top: 4px; }
  .address { font-size: 14px; line-height: 1.35; margin-top: 40px; }
  .contact-list { list-style: none; margin-top: 16px; font-size: 14px; line-height: 1.35; }
  .contact-list li { display: flex; align-items: center; gap: 10px; }
  .contact-list svg { width: 12px; height: 12px; fill: var(--gold); flex: none; }
</style>
</head>
<body>
<main class="canvas">
  <section class="card card-front" aria-label="Card front">
    <div class="brand-lockup">
      <span class="brand-square"></span>
      <span class="brand-name">dr Ternisu studio</span>
    </div>
  </section>

  <section class="card card-back" aria-label="Card back">
    <div class="gold-foil" role="img" aria-label="Crinkled gold foil texture"></div>
    <div class="info-panel">
      <p class="person-name">Radu Ionescu</p>
      <p class="person-role">President</p>
      <p class="address">24 Strada Lunga<br>Brasov, Romania 500058</p>
      <ul class="contact-list">
        <li><svg viewBox="0 0 12 12"><path d="M2.5 0.5 L4.5 2.8 L3.3 4.2 Q4.6 6.9 7.8 8.7 L9.2 7.5 L11.5 9.5 L10 11.5 Q4.5 11 0.5 2 Z"/></svg>0268-415-927</li>
        <li><svg viewBox="0 0 12 12"><path d="M3 0 H9 V12 H3 Z M4 1.5 V9 H8 V1.5 Z"/></svg>0722-318-604</li>
        <li><svg viewBox="0 0 12 12"><path d="M3 0 H9 V4 H3 Z M0.5 4.5 H11.5 V11 H0.5 Z"/></svg>0268-415-930</li>
        <li><svg viewBox="0 0 12 12"><path d="M0 2 H12 V10 H0 Z M1 3 L6 7 L11 3 Z" fill-rule="evenodd"/></svg>contact@ternisustudio.ro</li>
        <li><svg viewBox="0 0 12 12"><circle cx="6" cy="6" r="6"/></svg>www.ternisustudio.ro</li>
      </ul>
    </div>
  </section>
</main>
</body>
</html>
```